Wordpress Site Design for a Horror and Action Movie Production Company

We need a re-design/facelift of our website: https://k42t.pagecraft.io
The structure of the website could remain the same, but it needs to look and feel BETTER!

We would like the website coded in Wordpress so that it can be easily updated bu us, via adding new projects and new projects' info.

We specialize in Action, Horror, and Sci-Fi Genre. That being said, we don't want the website to look like it's a themed park with haunted houses. It should still be sharp and professional, as after all - it is a business for us!

Target Market(s)

Film Distribution Companies (B2B), as well as general audience that likes movies

Industry/Entity Type

Movie Production

Coding

Coded - Design and coding required

Number of Pages Required

5+ page

Font styles to use
Sans Serif

Colors

Designer to choose colors to be used in the design.

Requirements
Must have
• - PROJECTS page
• - Each PROJECT has a sub-page with project info/updates (up dates could be in a form of a WP post, ideally a template that we can use to update and create new PROJECT pages, with text, poster, and video link (trailer))
• - NEWS page that chronologically lists updates from all PROJECTS (could be done via WP blog)
• - HOME page would
Nice to have
• Should generally have a dark background.
• Websites we like as a reference of general approach and style:
• https://marbletoq.com
• https://velunpix.com (however this is very image-centric, and we might not have that much imagery at the moment)
• https://www.copperfieldechoandframe.com/other
• https://quennreels.com
Should not have
• We specialize in Action, Horror, and Sci-Fi Genre. That being said, we don't want the website to look like it's a themed park with haunted houses. It should still be sharp and professional, as after all - it is a business for us!

```html
<!DOCTYPE html>
<html lang="en">
<head>
<meta charset="utf-8">
<title>Kestrel 42 Media</title>
<link href="https://fonts.googleapis.com/css2?family=Montserrat:wght@500;600;800;900&family=Lato:wght@300;400&display=swap" rel="stylesheet">
<style>
:root{
  --ink:#0d0b0c;
  --black:#050505;
  --white:#ffffff;
  --gold:#c9a20f;
  --pink:#e6097c;
  --yellow:#c7ad10;
  --mint:#1db68c;
  --blue:#1a5df0;
  --leaf:#29a23c;
  --plum:#4e1e62;
  --muted:#cfcfcf;
  --head:'Montserrat',sans-serif;
  --body:'Lato',sans-serif;
}
*{margin:0;padding:0;box-sizing:border-box}
html,body{width:1200px;height:4229px;overflow:hidden;background:var(--ink);color:var(--white);font-family:var(--body)}
.page{position:relative;width:1200px;height:4229px;overflow:hidden}
.abs{position:absolute}
.center{left:0;right:0;text-align:center}
h1,h2,h3{font-family:var(--head);font-weight:800;letter-spacing:.08em}
.divider{width:16px;height:16px;background:var(--gold);transform:rotate(45deg);margin:0 auto;box-shadow:-10px 10px 0 -3px var(--white),10px -10px 0 -3px var(--white)}
/* header */
.site-header{top:0;left:0;width:1200px;height:121px;background:#151314;z-index:5}
.brand{left:88px;top:26px;width:206px;font-family:var(--head);font-weight:600;color:var(--white);text-align:center;letter-spacing:.06em;font-size:30px;line-height:32px}
.brand small{display:block;font-size:13px;line-height:18px;letter-spacing:.45em;border-bottom:2px solid var(--white);padding-bottom:4px;margin:0 12px}
.nav a{position:absolute;top:48px;font-family:var(--head);font-weight:500;font-size:18px;letter-spacing:.14em;color:var(--white);text-decoration:none}
.nav a.active{color:var(--gold)}
/* hero */
.hero-photo{top:121px;left:0;width:1200px;height:560px;background:radial-gradient(ellipse at 45% 30%,#5a5a5a 0%,#2c2c2c 45%,#111 100%)}
.hero-title{top:290px;font-size:80px;letter-spacing:.07em}
/* about */
.about-band{top:560px;left:0;width:1200px;height:611px}
.about-title{top:680px;font-size:53px}
.about-divider{top:752px;left:592px}
.about-text{top:812px;left:155px;width:890px;text-align:center;font-size:15.5px;line-height:29px;font-weight:300}
.about-text p{margin-bottom:21px}
/* feature panels */
.feature{top:1171px;width:600px;height:492px;text-align:center}
.feature.ent{left:0;background:radial-gradient(ellipse at 45% 40%,#8a1640 0%,#4a0a26 55%,#2a0616 100%)}
.feature.proj{left:600px;background:radial-gradient(ellipse at 60% 45%,#6a4a12 0%,#3b2b0d 55%,#1f1608 100%)}
.feature h2{margin-top:88px;font-size:57px}
.feature p{margin:34px auto 0;width:480px;font-size:15px;line-height:29.5px;font-weight:300}
.btn{display:inline-block;margin-top:38px;width:184px;height:69px;line-height:65px;border:2px solid var(--white);border-radius:35px;font-family:var(--head);font-weight:500;font-size:16px;letter-spacing:.1em}
/* video */
.video-title{top:1772px;font-size:55px}
.video-divider{top:1852px;left:592px}
.thumb{top:1911px;width:323px;height:240px}
.play{position:absolute;bottom:0;left:94px;width:135px;height:46px;background:var(--pink);border-radius:8px 8px 0 0;font-size:14px;letter-spacing:.06em;line-height:46px;text-align:center}
.arrow{top:2018px;font-size:28px;color:var(--white)}
/* services */
.services-bg{top:2265px;left:0;width:1200px;height:930px}
.svc{width:304px;height:256px;text-align:center;background-image:linear-gradient(135deg,transparent 55%,rgba(255,255,255,.06) 55%)}
.svc svg{margin-top:22px}
.svc h3{font-size:22px;font-weight:500;letter-spacing:.09em;margin-top:18px;white-space:nowrap}
.svc p{font-size:15px;line-height:27px;font-weight:300;margin:8px auto 0;width:250px}
/* partners */
.partners-title{top:3276px;font-size:56px}
.partners-divider{top:3357px;left:592px}
.partner-name{top:3717px;width:300px;text-align:center;font-family:var(--head);font-weight:500;font-size:22px;letter-spacing:.12em}
.dots{top:3792px;left:585px}
.dots span{display:inline-block;width:11px;height:11px;border-radius:50%;margin:0 3px;background:var(--white)}
.dots span:first-child{background:var(--gold)}
/* footer */
.social{top:4021px;width:52px;height:52px;border:2px solid var(--white);border-radius:50%;display:flex;align-items:center;justify-content:center}
.contact{top:4105px;font-size:15px;font-weight:400}
.contact .sep{margin:0 12px}
.footer-links{top:4145px;font-size:17px}
.footer-links .sep{margin:0 14px}
.copyright{top:4185px;font-size:13.5px;color:var(--muted)}
</style>
</head>
<body>
<div class="page">

  <div class="abs hero-photo" role="img" aria-label="Black and white still of a bearded man in a dark city street"></div>

  <header class="abs site-header">
    <div class="abs brand">KESTREL 42<small>MEDIA</small></div>
    <nav class="nav">
      <a class="active" style="left:543px">ABOUT</a>
      <a style="left:668px">NEWS</a>
      <a style="left:781px">PROJECTS</a>
      <a style="left:941px">CONTACT</a>
      <svg class="abs" style="left:1093px;top:50px" width="18" height="18" viewBox="0 0 18 18"><circle cx="7.5" cy="7.5" r="5.5" fill="none" stroke="#fff" stroke-width="2.5"/><line x1="11.5" y1="11.5" x2="16" y2="16" stroke="#fff" stroke-width="2.8"/></svg>
    </nav>
  </header>

  <h1 class="abs center hero-title">KESTREL 42 MEDIA</h1>

  <svg class="abs about-band" width="1200" height="611" viewBox="0 0 1200 611">
    <defs>
      <linearGradient id="aboutGrad" x1="0" y1="0" x2="0" y2="1">
        <stop offset="0" stop-color="#0c5a55"/>
        <stop offset=".55" stop-color="#139a72"/>
        <stop offset="1" stop-color="#1fe37a"/>
      </linearGradient>
      <linearGradient id="skylineGrad" x1="0" y1="0" x2="0" y2="1">
        <stop offset="0" stop-color="#050b08" stop-opacity="0"/>
        <stop offset=".35" stop-color="#050b08" stop-opacity=".85"/>
        <stop offset="1" stop-color="#050b08"/>
      </linearGradient>
    </defs>
    <path d="M0 105 Q600 -95 1200 105 L1200 611 L0 611 Z" fill="url(#aboutGrad)"/>
    <rect x="0" y="530" width="1200" height="81" fill="url(#skylineGrad)" role="img" aria-label="Silhouette of the Toronto city skyline"/>
  </svg>

  <h2 class="abs center about-title">ABOUT US</h2>
  <div class="abs divider about-divider"></div>
  <div class="abs about-text">
    <p>Kestrel 42 Media is a fresh brand of multi-media entertainment, aimed at development of original Canadian content as well as servicing of foreign productions in Toronto, Ontario, Canada.</p>
    <p>We produce genre feature films, series, documentaries, and anything else that we feel great about.<br>We take pride in our innovative approach to the process of filmmaking and marketing of our produced content. In simple terms, we make good looking motion picture content that is entertaining, visually compelling, and tells a good story.</p>
    <p>The decades of combined experience of the 4 founders of Kestrel 42 Media provide an unparalleled expertise of storytelling, production, sales and marketing of films.</p>
  </div>

  <section class="abs feature ent" role="img" aria-label="Performer on a stage lit in red and magenta">
    <h2>ENTERTAINMENT</h2>
    <p>Lorem ipsum dolor sit amet, consectetur adipiscing elit, sed do eiusmod tempor incididunt ut labore et dolore magna aliqua. Ut enim ad minim veniam, quis nostrud exercitation ullamco laboris nisi ut aliquip ex ea commodo consequat</p>
    <span class="btn">LEARN MORE</span>
  </section>
  <section class="abs feature proj" role="img" aria-label="Film still of two people embracing in warm amber light">
    <h2>PROJECTS</h2>
    <p>Lorem ipsum dolor sit amet, consectetur adipiscing elit, sed do eiusmod tempor incididunt ut labore et dolore magna aliqua. Ut enim ad minim veniam, quis nostrud exercitation ullamco laboris nisi ut aliquip ex ea commodo consequat</p>
    <span class="btn">LEARN MORE</span>
  </section>

  <h2 class="abs center video-title">WATCH VIDEO</h2>
  <div class="abs divider video-divider"></div>
  <span class="abs arrow" style="left:30px">&larr;</span>
  <span class="abs arrow" style="left:1145px">&rarr;</span>
  <div class="abs thumb" style="left:89px;background:linear-gradient(135deg,#6b5a54,#2d3346 60%,#b0907e)" role="img" aria-label="Video still of tattooed arms"><span class="play">&#9654; PLAY VIDEO</span></div>
  <div class="abs thumb" style="left:438px;background:linear-gradient(135deg,#5a0d12,#2a0508 55%,#8a1a1f)" role="img" aria-label="Video still of a dark red sci-fi machine interior"><span class="play">&#9654; PLAY VIDEO</span></div>
  <div class="abs thumb" style="left:788px;background:linear-gradient(160deg,#8f8f8f,#4c4c4c 60%,#6e6e6e)" role="img" aria-label="Black and white video still of a person lying down"><span class="play">&#9654; PLAY VIDEO</span></div>

  <svg class="abs services-bg" width="1200" height="930" viewBox="0 0 1200 930" role="img" aria-label="Dark monochrome battle scene">
    <defs>
      <radialGradient id="svcGrad" cx=".5" cy=".45" r=".7">
        <stop offset="0" stop-color="#3a3a3a"/>
        <stop offset="1" stop-color="#151515"/>
      </radialGradient>
    </defs>
    <path d="M0 0 Q600 150 1200 0 L1200 930 Q600 760 0 930 Z" fill="url(#svcGrad)"/>
  </svg>

  <div class="abs svc" style="left:118px;top:2466px;background-color:var(--pink)">
    <svg width="64" height="60" viewBox="0 0 64 60" fill="none" stroke="#fff" stroke-width="2"><rect x="4" y="14" width="40" height="30"/><circle cx="24" cy="30" r="8"/><path d="M22 26l6 4-6 4z"/><path d="M44 16l12-8v20l-12-4"/><line x1="10" y1="44" x2="10" y2="52"/><line x1="38" y1="44" x2="38" y2="52"/></svg>
    <h3>PRODUCTION</h3>
    <p>Lorem ipsum dolor sit amet, consectetur adipiscing elit, sed do eiusmod tempor incididunt</p>
  </div>
  <div class="abs svc" style="left:450px;top:2466px;background-color:var(--yellow)">
    <svg width="64" height="60" viewBox="0 0 64 60" fill="none" stroke="#fff" stroke-width="2"><rect x="10" y="16" width="44" height="30"/><circle cx="32" cy="14" r="10"/><path d="M29 9l7 5-7 5z"/><line x1="32" y1="46" x2="32" y2="54"/><line x1="20" y1="54" x2="44" y2="54"/></svg>
    <h3>DISTRIBUTION</h3>
    <p>Lorem ipsum dolor sit amet, consectetur adipiscing elit, sed do eiusmod tempor incididunt</p>
  </div>
  <div class="abs svc" style="left:778px;top:2466px;background-color:var(--mint)">
    <svg width="64" height="60" viewBox="0 0 64 60" fill="none" stroke="#fff" stroke-width="2"><rect x="10" y="16" width="44" height="32"/><circle cx="32" cy="30" r="9"/><line x1="23" y1="30" x2="41" y2="30"/><line x1="32" y1="21" x2="32" y2="39"/><path d="M24 4l8 12 8-12"/><line x1="24" y1="54" x2="40" y2="54"/></svg>
    <h3>TV CHANNELS</h3>
    <p>Lorem ipsum dolor sit amet, consectetur adipiscing elit, sed do eiusmod tempor incididunt</p>
  </div>
  <div class="abs svc" style="left:118px;top:2743px;background-color:var(--blue)">
    <svg width="64" height="60" viewBox="0 0 64 60" fill="none" stroke="#fff" stroke-width="2"><circle cx="32" cy="18" r="9"/><circle cx="32" cy="18" r="3"/><path d="M14 56V40l6-6 4 6v16M50 56V40l-6-6-4 6v16M26 56V44h12v12"/></svg>
    <h3>TECHNICAL SERVICES</h3>
    <p>Lorem ipsum dolor sit amet, consectetur adipiscing elit, sed do eiusmod tempor incididunt</p>
  </div>
  <div class="abs svc" style="left:450px;top:2743px;background-color:var(--leaf)">
    <svg width="64" height="60" viewBox="0 0 64 60" fill="none" stroke="#fff" stroke-width="2"><rect x="10" y="22" width="30" height="30"/><path d="M21 31l9 6-9 6z"/><rect x="28" y="6" width="26" height="22"/><line x1="33" y1="13" x2="49" y2="13"/><line x1="33" y1="20" x2="45" y2="20"/></svg>
    <h3>DIGITAL</h3>
    <p>Lorem ipsum dolor sit amet, consectetur adipiscing elit, sed do eiusmod tempor incididunt</p>
  </div>
  <div class="abs svc" style="left:778px;top:2743px;background-color:var(--plum)">
    <svg width="64" height="60" viewBox="0 0 64 60" fill="none" stroke="#fff" stroke-width="2"><path d="M14 30a18 18 0 0 1 32-11M50 30a18 18 0 0 1-32 11"/><path d="M46 12v8h-8M18 48v-8h8"/><path d="M32 40l-8-8a4 4 0 0 1 8-5 4 4 0 0 1 8 5z"/></svg>
    <h3>NEW PRODUCTS</h3>
    <p>Lorem ipsum dolor sit amet, consectetur adipiscing elit, sed do eiusmod tempor incididunt</p>
  </div>

  <h2 class="abs center partners-title">PARTNERS</h2>
  <div class="abs divider partners-divider"></div>
  <svg class="abs" style="left:0;top:3390px" width="1200" height="310" viewBox="0 0 1200 310">
    <defs>
      <linearGradient id="portraitGrad" x1="0" y1="0" x2="1" y2="1">
        <stop offset="0" stop-color="#8a8a8a"/>
        <stop offset="1" stop-color="#1e1e1e"/>
      </linearGradient>
    </defs>
    <g fill="none" stroke="#fff" stroke-width="2">
      <path d="M258 9 L402 153 L258 297 L114 153 Z"/>
      <path d="M599 9 L743 153 L599 297 L455 153 Z"/>
      <path d="M941 9 L1085 153 L941 297 L797 153 Z"/>
    </g>
    <path d="M258 25 L386 153 L258 281 L130 153 Z" fill="url(#portraitGrad)" role="img" aria-label="Black and white portrait of Rowan Pell"/>
    <path d="M599 25 L727 153 L599 281 L471 153 Z" fill="url(#portraitGrad)" role="img" aria-label="Black and white portrait of Milo Varsk"/>
    <path d="M941 25 L1069 153 L941 281 L813 153 Z" fill="url(#portraitGrad)" role="img" aria-label="Black and white portrait of Teodor Lane"/>
    <g fill="#050505" stroke="#fff" stroke-width="1.5">
      <circle cx="228" cy="39" r="5"/><circle cx="288" cy="267" r="5"/>
      <circle cx="569" cy="39" r="5"/><circle cx="629" cy="267" r="5"/>
      <circle cx="911" cy="39" r="5"/><circle cx="971" cy="267" r="5"/>
    </g>
  </svg>
  <div class="abs partner-name" style="left:108px">ROWAN PELL</div>
  <div class="abs partner-name" style="left:449px">MILO VARSK</div>
  <div class="abs partner-name" style="left:791px">TEODOR LANE</div>
  <div class="abs dots"><span></span><span></span></div>

  <svg class="abs" style="left:0;top:3860px" width="1200" height="369" viewBox="0 0 1200 369">
    <rect width="1200" height="369" fill="#1c1c1c"/>
    <path d="M0 0 L1200 0 L1200 20 Q600 180 0 20 Z" fill="#050505"/>
  </svg>

  <span class="abs social" style="left:481px" aria-label="Share link">
    <svg width="20" height="20" viewBox="0 0 20 20" fill="none" stroke="#fff" stroke-width="2"><path d="M8 12l4-4"/><path d="M9 5l2-2a3.5 3.5 0 0 1 5 5l-2 2"/><path d="M11 15l-2 2a3.5 3.5 0 0 1-5-5l2-2"/></svg>
  </span>
  <span class="abs social" style="left:542px" aria-label="Message">
    <svg width="20" height="20" viewBox="0 0 20 20" fill="none" stroke="#fff" stroke-width="2"><path d="M3 4h14v9H8l-4 3v-3H3z"/></svg>
  </span>
  <span class="abs social" style="left:604px" aria-label="Follow">
    <svg width="18" height="18" viewBox="0 0 18 18" stroke="#fff" stroke-width="2.2"><line x1="9" y1="2" x2="9" y2="16"/><line x1="2" y1="9" x2="16" y2="9"/></svg>
  </span>
  <span class="abs social" style="left:664px" aria-label="Video channel">
    <svg width="18" height="18" viewBox="0 0 18 18"><path d="M5 3l10 6-10 6z" fill="#fff"/></svg>
  </span>

  <div class="abs center contact">
    <svg width="11" height="14" viewBox="0 0 11 14"><path d="M5.5 0a5.5 5.5 0 0 0-5.5 5.5C0 9 5.5 14 5.5 14S11 9 11 5.5A5.5 5.5 0 0 0 5.5 0zm0 7.5a2 2 0 1 1 0-4 2 2 0 0 1 0 4z" fill="#fff"/></svg>
    7-208 HARBOUR LANE W., TORONTO, ON, M4X2B9, CANADA<span class="sep">|</span>
    <svg width="13" height="13" viewBox="0 0 13 13"><path d="M3 0l2 3-1.5 1.5a8 8 0 0 0 5 5L10 8l3 2-1.5 3C6 13 0 7 0 1.5z" fill="#fff"/></svg>
    555 014 2286<span class="sep">|</span>
    <svg width="15" height="11" viewBox="0 0 15 11"><rect width="15" height="11" fill="#fff"/><path d="M0 0l7.5 6L15 0" fill="none" stroke="#1c1c1c" stroke-width="1.5"/></svg>
    hello@kestrel42.example
  </div>
  <div class="abs center footer-links">About<span class="sep">/</span>News<span class="sep">/</span>Projects<span class="sep">/</span>Contact</div>
  <div class="abs center copyright">Copyrights &copy; 2019, The Company Name. All rights reserved.</div>

</div>
</body>
</html>
```